New Webpage for High Class Expert Witness Services Company

We are looking for a minimalist design for a webpage that just has our logo and an entry form offer to connect with one of our Liaisons.
The entry form should just ask for Name, Email, Contact Info and Description of Project.

Company Name is: The Marlowe Crest Advisory Services

Number of Pages Required

1 page

```html
<!DOCTYPE html>
<html lang="en">
<head>
<meta charset="utf-8">
<title>Marlowe Crest Advisory Services</title>
<link rel="stylesheet" href="https://fonts.googleapis.com/css2?family=Cinzel:wght@400;600;700&family=Roboto:wght@400&display=swap">
<style>
  :root {
    --ink: #1c1c1c;
    --ink-soft: #2e2e2e;
    --panel-dark: #141414;
    --panel-mid: #3a3a3c;
    --panel-light: #7c7c80;
    --field-line: #cfcfcf;
    --white: #ffffff;
    --bg-light: #efefef;
    --bg-mid: #b8b8b8;
    --bg-deep: #9a9a9a;
    --rule: #b4b4b4;
  }
  * { box-sizing: border-box; margin: 0; padding: 0; }
  html, body { width: 1200px; height: 741px; overflow: hidden; }
  body {
    position: relative;
    font-family: "Roboto", Arial, sans-serif;
    color: var(--ink);
    background:
      radial-gradient(ellipse 420px 520px at 560px 420px, var(--bg-deep) 0%, rgba(154,154,154,0) 100%),
      radial-gradient(ellipse 360px 300px at 230px 180px, #c9c9c9 0%, rgba(201,201,201,0) 100%),
      linear-gradient(90deg, var(--bg-light) 0%, var(--bg-mid) 35%, #c4c4c4 60%, var(--bg-light) 100%);
  }
  .backdrop-art {
    position: absolute; left: 350px; top: 115px; width: 364px; height: 480px;
    background: linear-gradient(160deg, rgba(220,220,220,0.55), rgba(160,160,160,0.25));
    opacity: 0.6;
  }
  .brand {
    position: absolute; left: 132px; top: 45px;
    display: flex; align-items: center; gap: 12px;
  }
  .brand-square { width: 52px; height: 52px; background: var(--ink-soft); }
  .brand-name {
    font-family: "Cinzel", Georgia, serif; font-weight: 600; color: var(--ink-soft);
    line-height: 1;
  }
  .brand-name .line-1 { display: block; font-size: 30px; letter-spacing: 0.5px; }
  .brand-name .line-2 { display: block; font-size: 17px; letter-spacing: 3px; margin-top: 6px; }
  .call {
    position: absolute; right: 115px; top: 42px;
    font-family: "Cinzel", Georgia, serif; font-size: 29px; color: var(--ink-soft);
    letter-spacing: 0.3px; white-space: nowrap;
  }
  .hero { position: absolute; left: 135px; top: 264px; }
  .hero-eyebrow {
    font-family: "Cinzel", Georgia, serif; font-size: 18px; letter-spacing: 2.5px;
    color: var(--ink-soft); margin-left: 4px; white-space: nowrap;
  }
  .hero-title {
    font-family: "Cinzel", Georgia, serif; font-weight: 400; font-size: 48px;
    line-height: 58px; letter-spacing: 2px; color: var(--ink); margin-top: 14px;
    white-space: nowrap;
  }
  .liaison {
    position: absolute; left: 714px; top: 122px; width: 377px; height: 436px;
    background:
      radial-gradient(ellipse 200px 110px at 300px 440px, rgba(150,150,155,0.85), rgba(150,150,155,0) 100%),
      radial-gradient(ellipse 240px 180px at 60px 120px, rgba(90,90,92,0.6), rgba(90,90,92,0) 100%),
      linear-gradient(135deg, var(--panel-mid) 0%, var(--panel-dark) 45%, #2a2a2c 80%, var(--panel-light) 100%);
  }
  .liaison-title {
    position: absolute; left: 45px; top: 36px;
    font-family: "Cinzel", Georgia, serif; font-weight: 400; font-size: 19px;
    line-height: 26px; color: var(--white); white-space: nowrap;
  }
  .field {
    position: absolute; left: 45px; width: 293px; height: 41px;
    background: transparent; border: 1px solid var(--field-line); border-radius: 2px;
    color: var(--white); font-family: "Roboto", Arial, sans-serif; font-size: 13.5px;
    padding: 0 17px; outline: none;
  }
  .field::placeholder { color: var(--white); opacity: 1; }
  .field-name { top: 86px; }
  .field-email { top: 143px; }
  .field-phone { top: 197px; }
  .field-message { top: 254px; height: 87px; padding-top: 12px; resize: none; }
  .submit {
    position: absolute; left: 45px; top: 354px; width: 296px; height: 44px;
    border: none; border-radius: 2px;
    background: linear-gradient(90deg, #d6d6d6 0%, #bdbdbd 50%, #8e8e90 100%);
    font-family: "Cinzel", Georgia, serif; font-weight: 700; font-size: 16px;
    color: var(--ink); letter-spacing: 0.5px;
  }
  .site-footer {
    position: absolute; left: 0; top: 677px; width: 1200px; height: 64px;
    border-top: 1px solid var(--rule);
    text-align: center; padding-top: 21px;
    font-size: 12px; color: var(--ink);
  }
</style>
</head>
<body>
  <div class="backdrop-art" role="img" aria-label="Faint abstract crest artwork in soft greys"></div>

  <header>
    <div class="brand">
      <span class="brand-square"></span>
      <span class="brand-name">
        <span class="line-1">MARLOWE CREST</span>
        <span class="line-2">ADVISORY SERVICES</span>
      </span>
    </div>
    <div class="call">CALL US 800-555-0142</div>
  </header>

  <section class="hero">
    <p class="hero-eyebrow">MARLOWE CREST ADVISORY SERVICES</p>
    <h1 class="hero-title">SEAMLESS<br>MEDICAL EXPERT<br>INTEGRATION</h1>
  </section>

  <form class="liaison">
    <h2 class="liaison-title">CONNECT WITH A LIAISON</h2>
    <input class="field field-name" type="text" placeholder="Name*">
    <input class="field field-email" type="email" placeholder="Email*">
    <input class="field field-phone" type="tel" placeholder="Phone number*">
    <textarea class="field field-message" placeholder="Description of Project"></textarea>
    <button class="submit" type="button">SUBMIT</button>
  </form>

  <footer class="site-footer">© 2026 Marlowe Crest Advisory Services. All Rights Reserved</footer>
</body>
</html>
```